Business Card for Professional Photographer

I'm looking for an eye catching modern clean design that compliments my logo/ website fonts & colours.
I specialise in architecture, corporate & commercial photography so I'm marketing to professional clients rather than portrait / wedding clients.

I would prefer to not have a solid black design.

My logo brand guide is as follows :

Main front font. : Reislust
Main font colour : #fff
Slogan front font : Ubuntu Bold
Monogram front font : Venti Medium
Container colour : #fff

I need print ready files in pdf .png & .eps formats.

Included in the files below are some screen grabs as reference to font & colours etc.

```html
<!DOCTYPE html>
<html lang="en">
<head>
<meta charset="utf-8">
<title>Clear Vantage – Business Card</title>
<link rel="stylesheet" href="https://fonts.googleapis.com/css2?family=Montserrat:wght@300&family=Open+Sans:wght@400;700&display=swap">
<style>
  :root {
    --page-bg: #d9d9d9;
    --card-bg: #333335;
    --gold-dark: #b8862f;
    --gold-mid: #d9aa4a;
    --gold-light: #f3d87a;
    --text-white: #ffffff;
  }
  * { margin: 0; padding: 0; box-sizing: border-box; }
  html, body {
    width: 1200px;
    height: 1125px;
    overflow: hidden;
    background: var(--page-bg);
  }
  .canvas {
    position: relative;
    width: 1200px;
    height: 1125px;
  }
  .card {
    position: absolute;
    left: 180px;
    width: 840px;
    height: 480px;
    background: var(--card-bg);
    box-shadow: 0 10px 30px rgba(0,0,0,0.25);
    overflow: hidden;
  }
  .card--back { top: 60px; }
  .card--front { top: 585px; }
  .card__edge {
    position: absolute;
    left: 0; right: 0; bottom: 0;
    height: 8px;
    background: linear-gradient(90deg, var(--gold-dark), var(--gold-light) 50%, var(--gold-mid));
  }
  .brand {
    position: absolute;
    display: flex;
    align-items: center;
    gap: 24px;
    white-space: nowrap;
  }
  .card--back .brand { left: 50%; top: 50%; transform: translate(-50%, -60%); }
  .card--front .brand { left: 50%; top: 105px; transform: translateX(-50%); }
  .brand__mark {
    width: 34px;
    height: 34px;
    background: var(--gold-mid);
    flex: none;
  }
  .brand__name {
    font-family: "Montserrat", sans-serif;
    font-weight: 300;
    font-size: 40px;
    letter-spacing: 7px;
    color: var(--text-white);
    text-transform: uppercase;
    line-height: 1;
  }
  .contact-block {
    position: absolute;
    left: 0; right: 0;
    top: 300px;
    display: flex;
    justify-content: center;
    align-items: stretch;
    gap: 30px;
  }
  .person { text-align: right; padding-top: 4px; }
  .person__name {
    font-family: "Open Sans", sans-serif;
    font-weight: 700;
    font-size: 31px;
    color: var(--gold-mid);
    text-transform: uppercase;
    line-height: 1.15;
    white-space: nowrap;
  }
  .person__role {
    font-family: "Open Sans", sans-serif;
    font-size: 23px;
    color: var(--text-white);
  }
  .divider {
    width: 2px;
    background: var(--gold-mid);
  }
  .contacts { list-style: none; }
  .contacts__item {
    display: flex;
    align-items: center;
    gap: 8px;
    font-family: "Open Sans", sans-serif;
    font-size: 24px;
    color: var(--text-white);
    line-height: 1.3;
    white-space: nowrap;
  }
  .contacts__icon { width: 20px; height: 20px; flex: none; }
</style>
</head>
<body>
<main class="canvas">

  <section class="card card--back" aria-label="Card back">
    <div class="brand">
      <span class="brand__mark"></span>
      <div class="brand__name">Clear Vantage</div>
    </div>
    <div class="card__edge"></div>
  </section>

  <section class="card card--front" aria-label="Card front">
    <div class="brand">
      <span class="brand__mark"></span>
      <div class="brand__name">Clear Vantage</div>
    </div>

    <div class="contact-block">
      <div class="person">
        <div class="person__name">Daniel Harrow</div>
        <div class="person__role">Director</div>
      </div>
      <div class="divider"></div>
      <ul class="contacts">
        <li class="contacts__item">
          <svg class="contacts__icon" viewBox="0 0 24 24" aria-hidden="true"><path fill="#d9aa4a" d="M6.6 10.8a15 15 0 0 0 6.6 6.6l2.2-2.2a1 1 0 0 1 1-.25 11.4 11.4 0 0 0 3.6.57 1 1 0 0 1 1 1V20a1 1 0 0 1-1 1A17 17 0 0 1 3 4a1 1 0 0 1 1-1h3.5a1 1 0 0 1 1 1c0 1.25.2 2.45.57 3.57a1 1 0 0 1-.25 1z"/></svg>
          555 014 2290
        </li>
        <li class="contacts__item">
          <svg class="contacts__icon" viewBox="0 0 24 24" aria-hidden="true"><rect x="2" y="5" width="20" height="14" rx="1" fill="#d9aa4a"/><path d="M2 6l10 7 10-7" fill="none" stroke="#333335" stroke-width="1.6"/></svg>
          info@clearvantage.com
        </li>
        <li class="contacts__item">
          <svg class="contacts__icon" viewBox="0 0 24 24" aria-hidden="true"><circle cx="12" cy="12" r="10" fill="#d9aa4a"/><path d="M2 12h20M12 2c3 3 3 17 0 20M12 2c-3 3-3 17 0 20" fill="none" stroke="#333335" stroke-width="1.4"/></svg>
          www.clearvantage.com
        </li>
      </ul>
    </div>
    <div class="card__edge"></div>
  </section>

</main>
</body>
</html>
```